Local Flower Farm Needs Business Card Design

I need business cards designed for a flower farm based in Eudora, Kansas.
Business Info:
We are a local cut flower farm located in Eudora, Kansas, founded by Corinne Haldwick. What started as a passion for agriculture and search for more joy in daily life has blossomed into a small business dedicated to providing the community with beautiful, fresh, and sustainable flowers. We specialize in local, seasonal blooms, ensuring that every petal reflects the care and dedication we pour into our craft. Our mission is to deliver the highest quality flowers directly to our customers through local farmers markets and to florists who share our commitment to sustainability. Join us in celebrating the beauty of nature, one bloom at a time!
Contact Details:
Corinne Haldwick
Owner
Phone 913-555-0147
Facebook: Rosalind Thorpe Gardens
Instagram: @RosalindThorpeGardens
Website: RosalindThorpeGardens.example
Target Market(s)
Wholesale to Florists and Direct to Consumer via Farmers Market
Industry/Entity Type
Florist, Farm
Contact Information for Business Card
Name, Contact Info, Logo
Look and feel
Each slider illustrates characteristics of the customer's brand and the style your logo design should communicate.

```html
<!DOCTYPE html>
<html lang="en">
<head>
<meta charset="utf-8">
<title>Rosalind Thorpe Gardens — Business Card</title>
<link rel="stylesheet" href="https://fonts.googleapis.com/css2?family=Arimo:wght@400;700&display=swap">
<style>
  :root {
    --backdrop: #d5d7d7;
    --card: #fbfbfa;
    --ink: #17201f;
    --muted: #6c6f6f;
    --rule: #3a3f3f;
    --faint: #ececea;
  }
  * { box-sizing: border-box; margin: 0; padding: 0; }
  html, body { width: 1200px; height: 829px; overflow: hidden; }
  body {
    background: var(--backdrop);
    font-family: "Arimo", Arial, sans-serif;
    color: var(--ink);
    position: relative;
  }
  .card {
    position: absolute;
    top: 260px;
    width: 520px;
    height: 297px;
    background: var(--card);
    box-shadow: 0 6px 18px rgba(0,0,0,.12);
  }
  .card--front { left: 50px; }
  .card--back { left: 630px; }

  .person { position: absolute; left: 34px; top: 36px; }
  .person__name { font-weight: 700; font-size: 21px; letter-spacing: .5px; text-transform: uppercase; }
  .person__role { font-size: 13px; color: var(--muted); margin-top: 2px; }
  .rule { position: absolute; height: 1px; background: var(--rule); }
  .rule--short { left: 34px; top: 84px; width: 140px; }
  .rule--long { left: 34px; top: 246px; width: 360px; }

  .contacts { position: absolute; left: 34px; top: 98px; list-style: none; }
  .contacts li { display: flex; align-items: center; gap: 7px; font-size: 14px; line-height: 22px; color: #2b3030; }
  .contacts svg, .web svg { width: 11px; height: 11px; flex: none; }

  .web { position: absolute; left: 210px; top: 256px; display: flex; align-items: center; gap: 7px; font-size: 14px; color: #2b3030; }

  .brand {
    position: absolute;
    display: flex; flex-direction: column; align-items: center; justify-content: center;
    text-align: center;
  }
  .brand__circle {
    border: 1px solid var(--ink);
    border-radius: 50%;
    display: flex; align-items: center; justify-content: center;
  }
  .brand__name { font-weight: 400; color: var(--ink); text-transform: uppercase; letter-spacing: 1.5px; line-height: 1.35; }
  .card--front .brand { left: 388px; top: 88px; }
  .card--front .brand__circle { width: 116px; height: 116px; }
  .card--front .brand__name { font-size: 11px; }
  .card--back .brand { left: 185px; top: 74px; }
  .card--back .brand__circle { width: 150px; height: 150px; }
  .card--back .brand__name { font-size: 14px; }
</style>
</head>
<body>
  <section class="card card--front" aria-label="Business card front">
    <div class="person">
      <h1 class="person__name">Corinne Haldwick</h1>
      <p class="person__role">Owner</p>
    </div>
    <div class="rule rule--short"></div>
    <ul class="contacts">
      <li>
        <svg viewBox="0 0 24 24" aria-hidden="true"><path fill="currentColor" d="M6.6 10.8a15 15 0 0 0 6.6 6.6l2.2-2.2a1 1 0 0 1 1-.25 11.4 11.4 0 0 0 3.6.57 1 1 0 0 1 1 1V20a1 1 0 0 1-1 1A17 17 0 0 1 3 4a1 1 0 0 1 1-1h3.5a1 1 0 0 1 1 1c0 1.25.2 2.45.57 3.57a1 1 0 0 1-.25 1z"/></svg>
        (913)555-0147
      </li>
      <li>
        <svg viewBox="0 0 12 12" aria-hidden="true"><circle cx="6" cy="6" r="5" fill="currentColor"/></svg>
        Rosalind Thorpe Gardens
      </li>
      <li>
        <svg viewBox="0 0 12 12" aria-hidden="true"><circle cx="6" cy="6" r="5" fill="currentColor"/></svg>
        @RosalindThorpeGardens
      </li>
    </ul>
    <div class="rule rule--long"></div>
    <p class="web">
      <svg viewBox="0 0 12 12" aria-hidden="true"><circle cx="6" cy="6" r="5" fill="currentColor"/></svg>
      RosalindThorpeGardens.example
    </p>
    <div class="brand">
      <div class="brand__circle"><span class="brand__name">Rosalind<br>Thorpe<br>Gardens</span></div>
    </div>
  </section>

  <section class="card card--back" aria-label="Business card back">
    <div class="brand">
      <div class="brand__circle"><span class="brand__name">Rosalind<br>Thorpe<br>Gardens</span></div>
    </div>
  </section>
</body>
</html>
```